Tallow Reed Software

We are a software company selling endpoint visibility, access and security technology to enterprise-level IT departments.

Our technology helps organizations gain comprehensive visibility into and control over devices accessing their corporate network so they can quickly identify and address suspicious activity on the network that could lead to potential threats like data breaches.

This technology can cost organizations upwards of $1M - depending on the size of the organization. Our primary clients are Pinnacle 2,000 companies.

We want a professional, polished business card to represent our new brand.

Info fields to include on the card:
Name
Job Title
Office Phone #
Cell Phone #
Email address
Address: 4270 Vestridge Pond Blvd., Ste. 2600, Bloomington, MN 55812
Website address: www.tallowreedsoftware.example
Tagline: Discover the edge. Optimize the whole.

Logo files and color specs document are attached. Would like color scheme to coordinate with the logo.

Also looking at stationary/envelope designs in conjunction with the business card designs. Received very few designs that included the stationary.

Software

```html
<!DOCTYPE html>
<html lang="en">
<head>
<meta charset="utf-8">
<title>Tallow Reed Software — Business Card</title>
<link href="https://fonts.googleapis.com/css2?family=PT+Sans:ital,wght@0,400;0,700;1,400&display=swap" rel="stylesheet">
<style>
  :root {
    --backdrop: #d3d0cf;
    --brand-red: #8a1f24;
    --card-white: #f6f5f4;
    --band-grey: #858585;
    --ink: #4a4a4a;
    --ink-soft: #5e5e5e;
    --rose: #d9b3a6;
    --rose-faint: #ede0db;
  }
  * { margin: 0; padding: 0; box-sizing: border-box; }
  html, body {
    width: 1200px; height: 1000px; overflow: hidden;
    background: var(--backdrop);
    font-family: "PT Sans", Arial, sans-serif;
  }
  .canvas { position: relative; width: 1200px; height: 1000px; }

  .card { position: absolute; width: 350px; height: 225px; overflow: hidden; }

  /* Front */
  .card-front {
    left: 196px; top: 466px;
    background: var(--brand-red);
    display: flex; align-items: center; justify-content: center; gap: 10px;
  }
  .brand-mark { width: 12px; height: 12px; background: #ffffff; transform: rotate(45deg); }
  .brand-name-front {
    color: #ffffff; font-weight: 700; font-size: 14px;
    letter-spacing: 2.5px; text-transform: uppercase;
  }

  /* Back */
  .card-back { left: 648px; top: 467px; background: var(--card-white); }
  .dot-field {
    position: absolute; left: 0; top: 12px; width: 130px; height: 200px;
    background: linear-gradient(90deg, var(--rose) 0%, var(--rose-faint) 70%, rgba(246,245,244,0) 100%);
    opacity: .55;
  }
  .holder { position: absolute; left: 27px; top: 38px; }
  .holder-name { font-size: 18px; color: var(--ink); line-height: 1; }
  .holder-title { font-size: 11px; font-style: italic; color: var(--ink-soft); margin-top: 4px; }

  .brand-band { position: absolute; left: 132px; top: 37px; width: 218px; height: 37px; }
  .brand-band svg { position: absolute; inset: 0; }
  .brand-band-label {
    position: absolute; left: 40px; top: 0; height: 37px;
    display: flex; align-items: center; gap: 7px;
    color: #ffffff; font-weight: 700; font-size: 10px;
    letter-spacing: 1.5px; text-transform: uppercase;
  }
  .brand-band-label .brand-mark { width: 8px; height: 8px; }

  .contact {
    position: absolute; right: 23px; top: 133px;
    text-align: right; font-size: 8.6px; line-height: 11.7px; color: var(--ink-soft);
  }
  .contact dt { display: inline; color: var(--brand-red); }
  .contact dd { display: inline; }
</style>
</head>
<body>
<main class="canvas">
  <section class="card card-front" aria-label="Card front">
    <span class="brand-mark" aria-hidden="true"></span>
    <span class="brand-name-front">Tallow Reed Software</span>
  </section>

  <section class="card card-back" aria-label="Card back">
    <div class="dot-field" role="img" aria-label="Faded dot pattern in soft rose tones"></div>

    <div class="holder">
      <p class="holder-name">Marten Oakley</p>
      <p class="holder-title">Managing Director</p>
    </div>

    <div class="brand-band">
      <svg width="218" height="37" viewBox="0 0 218 37" aria-hidden="true">
        <polygon points="12,0 218,0 218,37 0,37" fill="var(--band-grey)"/>
      </svg>
      <div class="brand-band-label">
        <span class="brand-mark" aria-hidden="true"></span>
        <span>Tallow Reed Software</span>
      </div>
    </div>

    <dl class="contact">
      <div><dt>Office Phone:</dt> <dd>555-0148-2290</dd></div>
      <div><dt>Cell Phone:</dt> <dd>555-0148-2290</dd></div>
      <div><dt>Email:</dt> <dd>contact@tallowreedsoftware.example</dd></div>
      <div><dt>Web:</dt> <dd>www.tallowreedsoftware.example</dd></div>
      <div><dt>Address:</dt> <dd>4270 Vestridge Pond Blvd.,</dd></div>
      <div><dd>Ste. 2600, Bloomington, MN 55812</dd></div>
    </dl>
  </section>
</main>
</body>
</html>
```